Business card for law firm

Need business card for new law firm. Think confident, authoritative, conservative, but not stuffy or old-fashioned.

Contact Information for Business Card

Content for card - logo (uploaded), plus the following:

Paul Whitcombe (larger font)
Managing Partner (larger font, but not as large as name)
Level 9, 7 Ferris Lane
Sydney NSW 2000
Main Tel 02 9364 2710
Direct Tel 02 8472 3159
Email paul@qvlegal.com.au
www.qvlegal.com.au

Letterhead design should include logo plus:
Level 9, 7 Ferris Lane
Sydney NSW 2000
Tel 02 8472 3159
www.qvlegal.com.au

```html
<!DOCTYPE html>
<html lang="en">
<head>
<meta charset="utf-8">
<title>Quayview Legal Letterhead</title>
<link rel="stylesheet" href="https://fonts.googleapis.com/css2?family=Lato:wght@400;500&family=Open+Sans:wght@400;600&display=swap">
<style>
  :root {
    --navy: #0b1e5b;
    --ink: #4a4a4a;
    --ink-strong: #333333;
    --paper: #ffffff;
  }
  html, body {
    margin: 0;
    padding: 0;
    width: 1040px;
    height: 1200px;
    overflow: hidden;
    background: var(--paper);
  }
  .letterhead {
    position: relative;
    width: 1040px;
    height: 1200px;
    background: var(--paper);
    font-family: "Open Sans", Arial, sans-serif;
    color: var(--ink);
  }
  .brand {
    position: absolute;
    top: 38px;
    right: 105px;
    text-align: right;
    color: var(--navy);
    font-family: "Open Sans", Arial, sans-serif;
    font-weight: 400;
  }
  .brand-square {
    display: block;
    width: 62px;
    height: 62px;
    background: var(--navy);
    margin: 0 58px 42px auto;
  }
  .brand-name {
    display: block;
    font-size: 40px;
    line-height: 40px;
    letter-spacing: 2px;
  }
  .brand-sub {
    display: block;
    font-size: 15px;
    line-height: 15px;
    letter-spacing: 16px;
    margin-top: 10px;
    margin-right: -16px;
    text-align: center;
  }
  .letter {
    position: absolute;
    left: 98px;
    top: 220px;
    width: 840px;
    font-size: 16.5px;
  }
  .issue-date { margin: 0; line-height: 22px; }
  .recipient { margin: 15px 0 0; line-height: 18px; }
  .salutation { margin: 50px 0 0; line-height: 22px; }
  .body-text p {
    margin: 27px 0 0;
    line-height: 27px;
    text-align: justify;
    hyphens: auto;
  }
  .body-text p:first-child { margin-top: 30px; }
  .closing { margin: 55px 0 0; line-height: 22px; }
  .signatory {
    margin: 48px 0 0;
    font-size: 20px;
    font-weight: 600;
    color: var(--ink-strong);
    line-height: 26px;
  }
  .signatory-title { margin: 4px 0 0; line-height: 22px; }
  .footer-band {
    position: absolute;
    left: 0;
    top: 1105px;
    width: 1040px;
    height: 62px;
    background: var(--navy);
    color: #ffffff;
    font-family: "Lato", Arial, sans-serif;
    font-weight: 500;
    font-size: 18.5px;
  }
  .footer-band span {
    position: absolute;
    top: 50%;
    transform: translateY(-50%);
    white-space: nowrap;
  }
  .footer-phone { left: 100px; }
  .footer-web { left: 303px; }
  .footer-address { right: 103px; }
</style>
</head>
<body>
<div class="letterhead">
  <div class="brand">
    <span class="brand-square"></span>
    <span class="brand-name">QUAYVIEW</span>
    <span class="brand-sub">LEGAL</span>
  </div>

  <div class="letter">
    <p class="issue-date">Issuing Date: May 5, 2018</p>
    <p class="recipient">Name Of Employee Mr. XYZABC<br>Address of Employee<br>Address Line 2 etc..</p>
    <p class="salutation">Dear Mr.XYZABC</p>
    <div class="body-text">
      <p>Lorem Ipsum has been the industry's standard dummy text ever since the 1500s, when an unknown printer took a galley of type and scrambled it to make a type specimen book. It has survived not only five centuries, but also the leap into electronic typesetting, remaining essentially unchanged. It was popularised in the 1960s with the release of Lettrafix sheets containing Lorem Ipsum passages, and more recently with desktop publishing software like Folio PageSet including versions of Lorem Ipsum.</p>
      <p>Lorem Ipsum is simply dummy text of the printing and typesetting industry. Lorem Ipsum has been the industry's standard dummy text ever since the 1500s, when an unknown printer took a galley of type and scrambled it to make a type specimen book.</p>
      <p>It has survived not only five centuries, but also the leap into electronic typesetting, remaining essentially unchanged. It was popularised in the 1960s with the release of Lettrafix sheets containing Lorem IpsumIpsum passages.</p>
    </div>
    <p class="closing">Yours Sincerely</p>
    <p class="signatory">Daniel Ashford</p>
    <p class="signatory-title">Managing Director</p>
  </div>

  <div class="footer-band">
    <span class="footer-phone">P: 02 8472 3159</span>
    <span class="footer-web">W: www.qvlegal.com.au</span>
    <span class="footer-address">Level 9, 7 Ferris Lane Sydney NSW 2000</span>
  </div>
</div>
</body>
</html>
```